Wesbite design for Investment Firm

We want a basic (clean) website that follows the form, fonts and colors of our attachments. This is for a financial investment management firm, but we have a boutique (anti-Wall Street) approach. Site should have an Home Page (Logo up top - room for basic copy on bottom, Philosophy Page (room for Quarterly Letter attachment and basic copy, Performance Page (room for Performance Overview and Performance Analysis and basic copy), Team Page, Commentary Page and Contact

Reason: Some designers have asked for an extension. Again, please only use image of Train Station or Train Station Logo in design.

Target Market(s)

Small and mid-size financial advisors from across the country

Industry/Entity Type

Financial

Number of Pages Required

5+ page

Font styles to use
Other font styles liked:
• Palotino Linotype

Colors
3176b5
cfdeed
ffffff

Requirements
Must have
• Please refer to existing site www.qlvor.example. Of note, this is too complex / cluttered. We simply want Blur, Grey and White consistent with attachments. The copy is pretty good, but will be simplified (and no quotes)
Should not have
• No images other than train station logo and / or train station image

```html
<!DOCTYPE html>
<html lang="en">
<head>
<meta charset="utf-8">
<title>Marlow Crest Investment Company</title>
<link rel="stylesheet" href="https://fonts.googleapis.com/css2?family=Lora:wght@400;500;700&family=Lato:wght@400;700&display=swap">
<style>
:root{
  --blue:#3176b5;
  --blue-dark:#2a66a0;
  --pale:#cfdeed;
  --mist:#e9eff6;
  --white:#ffffff;
  --ink:#3c4650;
  --grey:#6b737b;
  --panel:rgba(40,40,40,.88);
}
*{box-sizing:border-box;margin:0;padding:0}
html,body{width:1200px;height:2687px;overflow:hidden;background:var(--white)}
body{position:relative;font-family:"Lora",serif;color:var(--ink)}
.abs{position:absolute}
a{color:inherit}

.topbar{left:0;top:0;width:1200px;height:41px;background:var(--mist)}
.social-dot{position:absolute;width:30px;height:30px;border:2px solid var(--blue);border-radius:50%;top:6px}
.topbar .social-dot{background:var(--blue)}
.call{position:absolute;right:92px;top:10px;font:16px "Lora",serif;color:var(--blue);white-space:nowrap}
.call svg{vertical-align:-4px;margin:0 6px 0 14px}
.call em{color:var(--blue)}

.header{left:0;top:41px;width:1200px;height:100px;background:var(--white)}
.brand{position:absolute;left:79px;top:22px;font:400 24px "Lora",serif;color:var(--blue);padding-bottom:12px;border-bottom:1px solid #cfd6de;min-width:372px;white-space:nowrap}
.nav{position:absolute;left:506px;top:34px;display:flex;gap:10px;font:15px "Lora",serif;color:#555;white-space:nowrap}
.nav span{padding:6px 7px}
.nav .active{border:1px solid var(--blue);border-radius:5px;color:var(--blue)}

.hero{left:0;top:141px;width:1200px;height:574px;background:linear-gradient(180deg,#3b5877 0%,#24405e 55%,#1b3047 100%)}
.hero-title{left:0;top:150px;width:1200px;text-align:center;font:700 50px "Lora",serif;color:var(--white)}
.hero-copy{left:260px;top:233px;width:680px;text-align:center;font:700 14px/25px "Lora",serif;color:var(--white)}
.btn{left:496px;top:339px;width:210px;height:54px;border-radius:27px;background:var(--blue);color:var(--white);font:500 20px/54px "Lora",serif;text-align:center;letter-spacing:.5px}

.section-title{width:1200px;left:0;text-align:center;font:500 36px "Lora",serif;color:var(--blue)}
.rule{left:374px;width:452px;height:1px;background:#c9cfd6}
.rule::after{content:"";position:absolute;left:222px;top:-4px;width:8px;height:8px;border-radius:50%;background:#c9cfd6}

.pill{width:833px;height:129px;border-radius:65px}
.pill.solid{background:var(--blue);color:var(--white)}
.pill.soft{background:var(--pale);color:var(--ink)}
.pill h3{position:absolute;top:14px;font:500 25px "Lora",serif}
.pill.soft h3{color:var(--blue)}
.pill p{position:absolute;top:48px;width:640px;font:14px/25px "Lora",serif}
.pill b{font-weight:700}
.badge{position:absolute;top:14px;width:101px;height:101px;border-radius:50%;background:var(--white);border:4px solid var(--pale);display:flex;align-items:center;justify-content:center}
.badge i{width:80px;height:80px;border-radius:50%;background:var(--blue);display:flex;align-items:center;justify-content:center}
.pill.soft .badge{border-color:var(--blue)}

.band{left:0;top:1345px;width:1200px;height:500px;background:linear-gradient(100deg,#9aa3ab 0%,#c9b5a3 45%,#a8acb2 100%)}
.card{top:1393px;width:323px;height:396px;background:var(--panel);color:var(--white)}
.card h4{position:absolute;top:22px;font:500 36px "Lora",serif;padding-bottom:4px;border-bottom:1px solid #aaa;white-space:nowrap}
.report{position:absolute;left:90px;top:87px;width:142px;height:185px;background:#f4f6f8;border:1px solid #ccc}
.report-chart{position:absolute;left:10px;top:20px;width:120px;height:60px}
.card-copy{font:14px/25px "Lora",serif}
.year{font:500 19px "Lora",serif;position:relative;padding-left:24px}
.year::before{content:"";position:absolute;left:2px;top:8px;width:10px;height:10px;border-radius:50%;background:var(--white)}
.letter-link{font:14px/31px "Lora",serif;text-decoration:underline;white-space:nowrap}

.team-cell{top:2029px;width:238px;height:249px}
.photo{position:absolute;left:0;top:0;width:238px;height:210px;background:linear-gradient(180deg,#e4e4e6,#bdbfc3)}
.name{position:absolute;left:0;top:210px;width:238px;height:39px;background:var(--blue);color:var(--white);text-align:center;font:500 20px/39px "Lora",serif;white-space:nowrap}
.view-all{left:962px;top:2029px;width:238px;height:249px;background:linear-gradient(180deg,#6a94c2,#4f7fb4)}
.view-all span{position:absolute;left:0;top:112px;width:238px;text-align:center;font:500 20px "Lora",serif;color:var(--white);text-decoration:underline}

.footer{left:0;top:2278px;width:1200px;height:358px;background:var(--mist)}
.f-head{position:absolute;top:65px;font:500 21px "Lora",serif;color:var(--blue)}
.f-list{position:absolute;top:110px;list-style:none;font:14px/31px "Lora",serif;color:var(--grey)}
.f-list .on{color:var(--blue)}
.f-social{position:absolute;top:262px;width:52px;height:52px;border-radius:50%;border:2px solid var(--blue)}
.f-social.fill{background:var(--blue)}
.contact-row{position:absolute;left:605px;font:14px/24px "Lora",serif;color:var(--grey)}
.contact-row svg{position:absolute;left:0;top:2px}
.contact-row span{display:block;margin-left:33px}
.blog{position:absolute;width:105px;height:105px}
.copyright{left:0;top:2636px;width:1200px;height:51px;background:var(--blue);color:var(--white);text-align:center;font:14px/51px "Lora",serif;letter-spacing:.3px}
</style>
</head>
<body>

<div class="abs topbar">
  <span class="social-dot" style="left:78px"></span>
  <span class="social-dot" style="left:121px"></span>
  <span class="social-dot" style="left:162px"></span>
  <div class="call">Call us today
    <svg width="22" height="22" viewBox="0 0 24 24"><circle cx="12" cy="12" r="11" fill="none" stroke="#8a939c" stroke-width="1.5"/><path d="M8 6l2 3-1.3 1.4a8 8 0 0 0 4.9 4.9L15 14l3 2-1 2c-5 0-9-4-9-9z" fill="#8a939c"/></svg><em>555.010.7250</em></div>
</div>

<header class="abs header">
  <div class="brand">Marlow Crest Investment Company</div>
  <nav class="nav">
    <span class="active">Home</span><span>Philosophy</span><span>Performance</span><span>Team</span><span>Letters</span><span>Commentary</span><span>Contact</span>
  </nav>
</header>

<section class="abs hero" role="img" aria-label="Upward view of city office towers against a cloudy sky, tinted blue">
  <h1 class="abs hero-title">What is your next plan...?</h1>
  <p class="abs hero-copy">We founded Marlow Crest Investment Company in 1999, initially managing wealth from our family and friends in the town of Marlow Crest. The high expectations of our original investors is a key contributor to our value driven investment philosophy.</p>
  <div class="abs btn">LEARN MORE</div>
</section>

<h2 class="abs section-title" style="top:763px">Philosophy</h2>
<div class="abs rule" style="top:817px"></div>

<div class="abs pill solid" style="left:77px;top:851px">
  <h3 style="left:62px">Buy at a Discount</h3>
  <p style="left:62px">Our proprietary investment research seeks to determine the appraised value of a company. Investments are then made at a significant discount, ideally 20% to 40% below the company's current intrinsic value..... <b>READ MORE</b></p>
  <div class="badge" style="left:717px"><i><svg width="44" height="44" viewBox="0 0 24 24"><path d="M3 12l9-9h8v8l-9 9z" fill="#fff"/><circle cx="16.5" cy="7.5" r="1.5" fill="#3176b5"/><text x="10.5" y="15.5" font-size="8" font-family="Lato,sans-serif" font-weight="700" fill="#3176b5" text-anchor="middle">$</text></svg></i></div>
</div>

<div class="abs pill soft" style="left:290px;top:998px">
  <div class="badge" style="left:16px"><i style="background:var(--white)"><svg width="52" height="52" viewBox="0 0 24 24"><circle cx="10" cy="7" r="4" fill="#3176b5"/><path d="M2 21c0-5 3.5-8 8-8s8 3 8 8z" fill="#3176b5"/><path d="M16 12l5 9h-10z" fill="#fff" stroke="#3176b5" stroke-width="1"/><path d="M16 15v3" stroke="#3176b5" stroke-width="1.2"/></svg></i></div>
  <h3 style="left:134px">Emphasis on Risk</h3>
  <p style="left:134px">Our proprietary investment research seeks to determine the appraised value of a company. Investments are then made at a significant discount, ideally 20% to 40% below the company's current intrinsic value..... <b>READ MORE</b></p>
</div>

<div class="abs pill solid" style="left:77px;top:1143px">
  <h3 style="left:62px">Willingness to Hold Cash</h3>
  <p style="left:62px">Our proprietary investment research seeks to determine the appraised value of a company. Investments are then made at a significant discount, ideally 20% to 40% below the company's current intrinsic value..... <b>READ MORE</b></p>
  <div class="badge" style="left:717px"><i><svg width="46" height="46" viewBox="0 0 24 24"><circle cx="13" cy="7" r="5" fill="none" stroke="#fff" stroke-width="1.5"/><text x="13" y="9.8" font-size="7.5" font-family="Lato,sans-serif" font-weight="700" fill="#fff" text-anchor="middle">$</text><path d="M2 15h5l4 2h5a1.5 1.5 0 0 1 0 3H9M2 21h12l7-4" fill="none" stroke="#fff" stroke-width="1.5"/></svg></i></div>
</div>

<section class="abs band" role="img" aria-label="Soft-focus photo of people reading on a tablet in a bright room"></section>

<article class="abs card" style="left:77px">
  <h4 style="left:56px">Performance</h4>
  <div class="report">
    <svg class="report-chart" viewBox="0 0 120 60"><rect width="120" height="60" fill="#fff" stroke="#c8d3df"/><polyline points="4,52 20,46 34,40 48,42 62,30 76,26 90,18 104,14 116,8" fill="none" stroke="#3176b5" stroke-width="2"/></svg>
    <svg style="position:absolute;left:10px;top:92px" width="120" height="80" viewBox="0 0 120 80"><g fill="#9fb8d3"><rect x="4" y="40" width="10" height="36"/><rect x="20" y="28" width="10" height="48"/><rect x="36" y="46" width="10" height="30"/><rect x="52" y="20" width="10" height="56"/></g><g stroke="#c8cfd6"><line x1="72" y1="10" x2="116" y2="10"/><line x1="72" y1="24" x2="116" y2="24"/><line x1="72" y1="38" x2="116" y2="38"/><line x1="72" y1="52" x2="116" y2="52"/><line x1="72" y1="66" x2="116" y2="66"/></g></svg>
  </div>
  <p class="abs card-copy" style="left:28px;top:288px;width:270px;text-align:center">We believe trying to keep pace with the market in all environments promotes poor decisions...<u>READ MORE</u></p>
</article>

<article class="abs card" style="left:439px">
  <h4 style="left:45px">Letters</h4>
  <div class="abs" style="left:42px;top:88px">
    <div class="year">2017</div>
    <div class="letter-link">Adviser Letter – 2017 Q2</div>
    <div class="letter-link">Adviser Letter – 2017 Q1</div>
    <div class="year" style="margin-top:10px">2016</div>
    <div class="letter-link">Adviser Letter – 2017 Q4</div>
    <div class="letter-link">Adviser Letter – 2017 Q3</div>
    <div class="letter-link">Adviser Letter – 2017 Q2</div>
    <div class="letter-link" style="margin-top:14px">READ MORE</div>
  </div>
</article>

<article class="abs card" style="left:801px">
  <h4 style="left:45px">Commentary</h4>
  <div class="abs" style="left:45px;top:86px;width:250px;font:500 20px/25px 'Lora',serif">Core Equity Portfolio<br>– Q2 2017</div>
  <div class="abs" style="left:45px;top:153px;font:500 14px 'Lora',serif">August 10, 2017</div>
  <p class="abs card-copy" style="left:45px;top:196px;width:238px">Based on our estimate of fair value relative to the company's current stock price, we determine each company's current margin of safety in the Core Equity .....<u>READ MORE</u></p>
</article>

<h2 class="abs section-title" style="top:1900px">Meet Our Team</h2>
<div class="abs rule" style="top:1956px"></div>

<div class="abs team-cell" style="left:0"><div class="photo" role="img" aria-label="Portrait of a team member in business attire"></div><div class="name">Laura J. Penfield</div></div>
<div class="abs team-cell" style="left:241px"><div class="photo" role="img" aria-label="Portrait of a team member in a grey suit"></div><div class="name">Warren R. Hale</div></div>
<div class="abs team-cell" style="left:482px"><div class="photo" role="img" aria-label="Portrait of a team member in a dark suit"></div><div class="name">James M. Orrin</div></div>
<div class="abs team-cell" style="left:722px"><div class="photo" role="img" aria-label="Portrait of a team member"></div><div class="name">Ava Linden</div></div>
<div class="abs view-all" role="img" aria-label="Faded portrait behind a view all link">
  <svg class="abs" style="left:104px;top:72px" width="30" height="30" viewBox="0 0 24 24"><circle cx="10" cy="10" r="7" fill="none" stroke="#fff" stroke-width="2"/><path d="M15 15l6 6M7 10h6M10 7v6" stroke="#fff" stroke-width="2"/></svg>
  <span>VIEW ALL</span>
</div>

<footer class="abs footer">
  <div class="f-head" style="left:81px">Quick Links</div>
  <ul class="f-list" style="left:81px"><li>Performance Overview</li><li>Performance Analysis</li><li>Verification Statement</li><li>Marlow Crest ADV Part 2</li></ul>
  <span class="f-social fill" style="left:77px"></span>
  <span class="f-social" style="left:149px"></span>
  <span class="f-social" style="left:222px"></span>

  <div class="f-head" style="left:387px">Usefull Links</div>
  <ul class="f-list" style="left:387px"><li class="on">Home</li><li>Philosophy</li><li>Performance</li><li>Team</li><li>Letters</li><li>Commentary</li><li>Contact</li></ul>

  <div class="f-head" style="left:605px">Get In Touch</div>
  <div class="contact-row" style="top:126px"><svg width="16" height="22" viewBox="0 0 16 22"><path d="M8 0a8 8 0 0 0-8 8c0 6 8 14 8 14s8-8 8-14a8 8 0 0 0-8-8z" fill="#3176b5"/><circle cx="8" cy="8" r="3" fill="#e9eff6"/></svg><span>1200 Elm Meadow Avenue,<br>Suite 210 Dallas, TX 75201</span></div>
  <div class="contact-row" style="top:192px"><svg width="20" height="20" viewBox="0 0 24 24"><path d="M5 2l4 5-2 3a12 12 0 0 0 7 7l3-2 5 4-2 3C11 22 2 13 2 4z" fill="#3176b5"/></svg><span>555.010.7250</span></div>
  <div class="contact-row" style="top:240px"><svg width="22" height="18" viewBox="0 0 22 18"><rect x="1" y="1" width="20" height="16" fill="none" stroke="#3176b5" stroke-width="2"/><path d="M1 2l10 8 10-8" fill="none" stroke="#3176b5" stroke-width="2"/></svg><span>info@mcic.example</span></div>

  <div class="f-head" style="left:906px">Latest Blog</div>
  <div class="blog" role="img" aria-label="Blog photo of a smiling person" style="left:905px;top:106px;background:linear-gradient(135deg,#c9a48a,#6d5a52)"></div>
  <div class="blog" role="img" aria-label="Blog photo of coins and papers" style="left:1019px;top:106px;background:linear-gradient(135deg,#d8c6a6,#9c8766)"></div>
  <div class="blog" role="img" aria-label="Blog photo of a highway interchange" style="left:905px;top:228px;background:linear-gradient(135deg,#7a9a6a,#4f5e52)"></div>
  <div class="blog" role="img" aria-label="Blog photo of a person at work" style="left:1019px;top:228px;background:linear-gradient(135deg,#9fb2c8,#c2774a)"></div>
</footer>

<div class="abs copyright"><b>MARLOW CREST INVESTMENT COMPANY</b> | Copyright 2017 .All Rights Reserved</div>

</body>
</html>
```